Beacon Advisory Website

I currently have a website www.beaconadvisoryinc.com. We are a IT Consulting Company. Our website will pretty much tell out our services. I am looking to enhance my website and make it look more professional. Looking for very classy and Contemporary look and design for my website.

It Company

```html
<!DOCTYPE html>
<html lang="en">
<head>
<meta charset="utf-8">
<title>Beacon Advisory</title>
<link href="https://fonts.googleapis.com/css2?family=Oswald:wght@500;600&family=Roboto:wght@400;500&family=Lato:wght@300;400;700&family=Poiret+One&family=Comfortaa:wght@400&display=swap" rel="stylesheet">
<style>
:root{
  --blue:#1d5fa8;
  --sky:#11a3dc;
  --navy:#123a7a;
  --ink:#333;
  --muted:#8a8a8a;
  --line:#e4e4e4;
  --dark:#10151d;
  --white:#fff;
}
*{margin:0;padding:0;box-sizing:border-box}
html,body{width:1200px;height:3093px;overflow:hidden;background:var(--white)}
body{font-family:'Lato',sans-serif;color:var(--ink);position:relative}
section{position:absolute;left:0;width:1200px;overflow:hidden}
.fill{position:absolute;inset:0}

/* hero */
.hero{top:0;height:660px}
.hero .fill{background:linear-gradient(100deg,#f3eef0 0%,#e7e3e8 35%,#cfc6c4 60%,#a99f9c 80%,#d8d2d4 100%)}
.hero .fill::after{content:"";position:absolute;inset:0;background:linear-gradient(180deg,rgba(255,255,255,.55),rgba(255,255,255,.25) 60%,rgba(240,230,240,.5))}
.brand{position:absolute;left:82px;top:44px;display:flex;align-items:center;gap:14px}
.brand-mark{width:46px;height:46px;background:var(--blue)}
.brand-name{font-family:'Lato',sans-serif;font-weight:700;font-size:34px;color:var(--blue);letter-spacing:1px}
.nav{position:absolute;top:64px;left:536px;display:flex;gap:0}
.nav a{font-family:'Roboto',sans-serif;font-size:15px;color:var(--blue);text-decoration:none;padding:0 22px 12px;display:block}
.nav a.active{color:#222;border-bottom:2px solid #555}
.hero-title{position:absolute;top:284px;left:0;width:1200px;text-align:center;font-family:'Oswald',sans-serif;font-weight:600;font-size:60px;color:var(--navy);letter-spacing:-0.5px}
.call{position:absolute;top:384px;left:0;width:1200px;display:flex;justify-content:center;align-items:center;gap:20px;font-family:'Oswald',sans-serif;color:var(--navy)}
.call .label{font-size:29px;font-weight:500;color:var(--blue)}
.call .ico{width:62px;height:62px;border-radius:50%;background:var(--blue);display:flex;align-items:center;justify-content:center}
.call .num{font-size:32px;font-weight:500}
.btn{position:absolute;top:474px;left:507px;width:186px;height:62px;background:var(--sky);color:#fff;font-family:'Roboto',sans-serif;font-size:24px;display:flex;align-items:center;justify-content:center}

/* about */
.about{top:660px;height:464px}
.sec-title{font-family:'Poiret One',sans-serif;font-size:58px;color:var(--blue);line-height:1;letter-spacing:1px;position:absolute;left:80px}
.intro{position:absolute;left:398px;width:716px;font-size:15.5px;line-height:31px;color:var(--muted)}
.about .sec-title{top:68px}
.about .intro{top:68px}
.features{position:absolute;top:258px;left:72px;width:1060px;display:flex}
.feature{flex:1;display:flex;gap:20px;padding:0 28px 0 0;border-right:1px solid var(--line);margin-right:38px;height:150px}
.feature:last-child{border:none;margin:0}
.feature svg{flex:none}
.feature h3{font-weight:400;font-size:20px;color:#333;margin:10px 0 14px}
.feature p{font-size:13.5px;line-height:21px;color:var(--muted)}

/* band */
.band{top:1124px;height:309px}
.band .fill{background:linear-gradient(90deg,#1a1f27,#2e3440 45%,#232830 70%,#15191f)}
.band .fill::after{content:"";position:absolute;inset:0;background:rgba(10,12,16,.45)}
.quote{position:absolute;top:122px;left:0;width:1200px;text-align:center;font-family:'Comfortaa',sans-serif;font-size:20px;line-height:31px;color:#fff}

/* services */
.services{top:1433px;height:619px}
.services .sec-title{top:72px;line-height:52px}
.services .intro{top:64px;color:#666;font-size:14.5px;line-height:26px}
.svc{position:absolute;top:227px;width:300px;text-align:center}
.svc svg{display:block;margin:0 auto}
.svc h3{font-weight:400;font-size:21px;color:#222;margin:24px 0 12px;letter-spacing:.5px}
.svc p{font-size:13.5px;line-height:22px;color:var(--muted);padding:0 6px}

/* solutions */
.solutions{top:2052px;height:416px}
.solutions .fill{background:radial-gradient(ellipse at 70% 40%,#3b4a60 0%,#1c2636 45%,#0b0f16 100%)}
.solutions .sec-title{top:68px;color:#fff}
.solutions .intro{top:54px;left:452px;width:640px;color:#e8e8e8;font-size:13.5px;line-height:26px}
.sol{position:absolute;top:160px;width:190px;text-align:center}
.sol-label{position:absolute;top:66px;left:0;width:190px;color:#fff;font-family:'Roboto',sans-serif;font-weight:500;font-size:14px;line-height:17px;text-transform:uppercase}

/* contact */
.contact{top:2468px;height:625px}
.contact .fill{background:linear-gradient(135deg,#e9e6df,#ece9e2 50%,#e2e6dc)}
.card{position:absolute;left:78px;top:58px;width:386px;height:518px;background:rgba(255,255,255,.95);padding:50px 0 0 68px}
.card h2{font-family:'Poiret One',sans-serif;font-weight:400;font-size:31px;color:#333;margin:0 0 18px}
.office{margin-bottom:22px}
.office h3{display:flex;align-items:center;gap:12px;font-weight:400;font-size:20px;color:var(--sky);margin-left:-4px;margin-bottom:10px}
.office p{font-size:13.5px;line-height:21px;color:#555;padding-left:52px}
.pin{position:absolute;left:676px;top:132px}
</style>
</head>
<body>

<section class="hero">
  <div class="fill" role="img" aria-label="Photo of business people in discussion at a laptop"></div>
  <div class="brand"><span class="brand-mark"></span><span class="brand-name">BEACON ADVISORY</span></div>
  <nav class="nav">
    <a class="active">Home</a><a>About Us</a><a>Services</a><a>Resources</a><a>Career</a><a>Contact Us</a>
  </nav>
  <h1 class="hero-title">DELIVERING EXCEPTIONAL CLIENT SERVICE</h1>
  <div class="call">
    <span class="label">CALL US ON</span>
    <span class="ico"><svg width="30" height="30" viewBox="0 0 24 24"><path fill="#fff" d="M6.6 10.8c1.4 2.8 3.8 5.1 6.6 6.6l2.2-2.2c.3-.3.7-.4 1-.2 1.1.4 2.3.6 3.6.6.6 0 1 .4 1 1V20c0 .6-.4 1-1 1C10.6 21 3 13.4 3 4c0-.6.4-1 1-1h3.5c.6 0 1 .4 1 1 0 1.3.2 2.5.6 3.6.1.3 0 .7-.2 1z"/></svg></span>
    <span class="num">+1 (555) 014 2290</span>
  </div>
  <a class="btn">CONTACT US</a>
</section>

<section class="about">
  <h2 class="sec-title">ABOUT US</h2>
  <p class="intro">Today's IT market is a dynamic, fast-paced industry, with ever-increasing demands. Meeting these demands for over 25 years, Beacon Advisory maintains a global presence, aggressively recruiting expertly qualified IT and Management Professionals from around the world and cultivating key partnerships with corporations to understand their business models end-to-end.</p>
  <div class="features">
    <div class="feature">
      <svg width="44" height="50" viewBox="0 0 44 50"><circle cx="22" cy="20" r="14" fill="none" stroke="#999" stroke-width="2"/><rect x="16" y="36" width="12" height="8" fill="#999"/></svg>
      <div><h3>Consulting</h3><p>Beacon Advisory has certified professional consultants to work with you to help increase the business.</p></div>
    </div>
    <div class="feature">
      <svg width="56" height="56" viewBox="0 0 56 56"><circle cx="28" cy="28" r="26" fill="#999"/><circle cx="28" cy="22" r="9" fill="#fff"/><path d="M12 46c3-9 9-12 16-12s13 3 16 12" fill="#fff"/></svg>
      <div><h3>Staff Augmentation</h3><p>For years Beacon Advisory has been offering our customers the ability to augment their existing staff</p></div>
    </div>
    <div class="feature">
      <svg width="50" height="50" viewBox="0 0 50 50"><circle cx="25" cy="22" r="16" fill="#999"/><rect x="21" y="38" width="8" height="8" fill="#999"/></svg>
      <div><h3>Offshore</h3><p>Our Offshore development model has a unique distinction of providing efficient software solutions</p></div>
    </div>
  </div>
</section>

<section class="band">
  <div class="fill" role="img" aria-label="Dark photo of business people working at a desk"></div>
  <p class="quote">Effective integration of information technology into an<br>organization's business processes has become increasingly<br>crucial to prosperity</p>
</section>

<section class="services">
  <h2 class="sec-title">OUR<br>SERVICES</h2>
  <p class="intro">IT includes such items as the systems software, application software, computer hardware, networks and databases associated with managing an organization's information. The chief information officer leads the department that manages most aspects of an organization's IT.</p>

  <div class="svc" style="left:163px">
    <svg width="200" height="200" viewBox="0 0 200 200"><path d="M40 20 Q100 0 170 30 Q200 100 170 170 Q100 200 30 170 Q0 100 40 20Z" fill="none" stroke="#8ccbea" stroke-width="8"/><rect x="52" y="52" width="96" height="96" rx="6" fill="#fff" transform="rotate(-8 100 100)"/><circle cx="92" cy="104" r="14" fill="none" stroke="#999" stroke-width="7"/><path d="M100 110 L130 80" stroke="#999" stroke-width="8"/></svg>
    <h3>DEVELOPMENT</h3>
    <p>Drawing on our experience in all major industries, we develop solutions that meet the most challenging IT problems.</p>
  </div>
  <div class="svc" style="left:450px">
    <svg width="200" height="200" viewBox="0 0 200 200"><path d="M40 20 Q100 0 170 30 Q200 100 170 170 Q100 200 30 170 Q0 100 40 20Z" fill="none" stroke="#1582c5" stroke-width="8"/><rect x="76" y="76" width="50" height="50" fill="#1582c5"/><circle cx="90" cy="90" r="6" fill="none" stroke="#fff" stroke-width="3"/><circle cx="112" cy="112" r="6" fill="none" stroke="#fff" stroke-width="3"/><path d="M95 95 L107 107" stroke="#fff" stroke-width="3"/></svg>
    <h3>TECHNOLOGY</h3>
    <p>Beacon Advisory Training programs are perfect for individuals to enhance their careers. Our hands-on practical.</p>
  </div>
  <div class="svc" style="left:739px">
    <svg width="200" height="200" viewBox="0 0 200 200"><path d="M40 20 Q100 0 170 30 Q200 100 170 170 Q100 200 30 170 Q0 100 40 20Z" fill="none" stroke="#8ccbea" stroke-width="8"/><circle cx="100" cy="96" r="18" fill="#999"/><rect x="92" y="110" width="14" height="12" fill="#999"/></svg>
    <h3>IT CONSULTING</h3>
    <p>Information technology should improve business results. Our team helps companies make sure it does. We look at IT issues.</p>
  </div>
</section>

<section class="solutions">
  <div class="fill" role="img" aria-label="Dark technology backdrop with city and data graphics"></div>
  <h2 class="sec-title">SOLUTIONS</h2>
  <p class="intro">We understand the complexities management faces when staffing a project. It isn't enough to simply supply a list of skilled and available candidates. Instead, we work hand in hand with you to provide a customized pool of talented professionals, uniquely qualified to make your project a success</p>

  <div class="sol" style="left:249px">
    <svg width="190" height="220" viewBox="0 0 190 220"><path d="M28 120 A70 70 0 1 1 162 120" fill="none" stroke="#fff" stroke-width="10"/><circle cx="95" cy="172" r="36" fill="#fff"/><circle cx="95" cy="172" r="15" fill="none" stroke="#222" stroke-width="3"/><path d="M95 172 L104 164" stroke="#222" stroke-width="3"/></svg>
    <span class="sol-label" style="top:96px">Dashboard</span>
  </div>
  <div class="sol" style="left:505px">
    <svg width="190" height="220" viewBox="0 0 190 220"><path d="M28 120 A70 70 0 1 1 162 120" fill="none" stroke="#fff" stroke-width="10"/><circle cx="95" cy="172" r="36" fill="#fff"/><circle cx="95" cy="172" r="15" fill="#222"/><circle cx="95" cy="172" r="6" fill="#fff"/></svg>
    <span class="sol-label" style="top:88px">Data<br>Warehousing</span>
  </div>
  <div class="sol" style="left:763px">
    <svg width="190" height="220" viewBox="0 0 190 220"><path d="M28 120 A70 70 0 1 1 162 120" fill="none" stroke="#fff" stroke-width="10"/><circle cx="95" cy="172" r="36" fill="#fff"/><ellipse cx="92" cy="162" rx="13" ry="5" fill="#222"/><rect x="79" y="164" width="26" height="18" fill="#222"/><circle cx="106" cy="182" r="7" fill="#222" stroke="#fff" stroke-width="2"/></svg>
    <span class="sol-label" style="top:96px">BPM</span>
  </div>
</section>

<section class="contact">
  <div class="fill" role="img" aria-label="Street map showing the technical center location"></div>
  <svg class="pin" width="24" height="34" viewBox="0 0 24 34"><path d="M12 0C5 0 0 5 0 12c0 9 12 22 12 22s12-13 12-22C24 5 19 0 12 0z" fill="#d9342b"/><circle cx="12" cy="12" r="4" fill="#8a1a14"/></svg>
  <div class="card">
    <h2>KEEP IN TOUCH</h2>
    <div class="office">
      <h3><svg width="40" height="28" viewBox="0 0 40 28"><rect x="6" y="4" width="12" height="24" fill="#11a3dc"/><rect x="20" y="10" width="12" height="18" fill="#11a3dc"/></svg>Head Office</h3>
      <p>480 Harbor Lane<br>Suite 120<br>Westfield, NJ 07090</p>
    </div>
    <div class="office">
      <h3><svg width="40" height="28" viewBox="0 0 40 28"><circle cx="18" cy="14" r="13" fill="#11a3dc"/><path d="M8 14h20M18 1v26" stroke="#fff" stroke-width="2"/></svg>Technical Center</h3>
      <p>2710 Maple Ridge Road<br>Suite 310<br>Oakdale MI 48210</p>
    </div>
    <div class="office">
      <h3><svg width="40" height="28" viewBox="0 0 40 28"><rect x="8" y="1" width="20" height="27" fill="#11a3dc"/><path d="M12 6h4M20 6h4M12 12h4M20 12h4M12 18h4M20 18h4" stroke="#fff" stroke-width="2"/></svg>West Coast Office</h3>
      <p>1560 Bayview Court<br>Suite 400<br>Fairmont, CA 95020</p>
    </div>
  </div>
</section>

</body>
</html>
```